Stylish High End Wedding Videography/Films Website (BMRT)

We need a modern and high-end website look for our wedding video and films business. We films weddings all over the United Kingdom and at European destinations so need something to reflect our work. The website should be visually stunning with images and videos being the focal point as this is what our services are;

I have uploads of some items I like and the features the site needs to have. These have been taken from other websites using standout features.

We need the following pages;

1 - Homepage
2 - Films Index Page
3 - Individual Films Page
4 - Prices / Collection Page
5 - Reviews
6 - Options
7 - About
8 - Contact
9 - Blog Index
10 - Blog Page

All pages must be consistent so have a similar style.

Pages on menu:
Films
Prices
Reviews
Options
About
Contact

We require a responsive look too. Over 90% of our visitors access the website via their mobile devices.

Please use the colours from our logo to incorporate into the website.

Target Market(s)

Wedding Couples

Industry/Entity Type

Wedding Photography

Number of Pages Required

5+ page

Font styles to use
Sans Serif
Script

Requirements
Must have
• The logo must be in the centre of the menu at the top.

Social icons at the bottom of the page.

Use only two fonts including Lore which is supplied
Nice to have
• Different video for each page on the top header. This will play behind the menu.

```html
<!DOCTYPE html>
<html lang="en">
<head>
<meta charset="utf-8">
<title>BMRT Wedding Films</title>
<link href="https://fonts.googleapis.com/css2?family=Montserrat:wght@400;500;600;700&display=swap" rel="stylesheet">
<style>
:root{
  --gold:#a68b4c;
  --gold-band:#9b8449;
  --espresso:#433a35;
  --ink:#2f2a27;
  --muted:#6b6460;
  --mist:#f6f6f6;
  --white:#ffffff;
}
*{margin:0;padding:0;box-sizing:border-box}
html,body{width:1200px;height:4201px;overflow:hidden}
body{font-family:'Montserrat',sans-serif;color:var(--ink);background:var(--white);position:relative}
.abs{position:absolute}
.photo{position:absolute}
.dot{display:inline-block;width:3px;height:3px;border-radius:50%;background:var(--ink);vertical-align:middle}

/* hero */
.hero{position:absolute;left:0;top:0;width:1200px;height:650px}
.hero-photo{left:459px;top:0;width:741px;height:650px;
  background:
    radial-gradient(ellipse 30% 26% at 95% 14%,rgba(236,168,92,.85),rgba(236,168,92,0) 100%),
    radial-gradient(ellipse 22% 60% at 62% 48%,rgba(222,222,226,.75),rgba(222,222,226,0) 100%),
    radial-gradient(ellipse 18% 45% at 20% 30%,rgba(190,196,200,.55),rgba(190,196,200,0) 100%),
    radial-gradient(ellipse 30% 30% at 8% 70%,rgba(70,90,45,.7),rgba(70,90,45,0) 100%),
    linear-gradient(180deg,#6d5b47 0%,#3b3934 45%,#2a2a28 75%,#1c1c1b 100%)}
.nav{position:absolute;top:50px;font-size:12px;color:var(--ink);display:flex;gap:28px;align-items:center}
.nav a{color:inherit;text-decoration:none}
.nav.left{left:96px}
.nav.left a.active{color:var(--gold)}
.nav.right{left:852px;color:var(--white)}
.nav.right .dot{background:var(--white)}
.brand{position:absolute;left:500px;top:62px;width:200px;text-align:center;color:var(--white)}
.brand b{display:block;font-size:18px;font-weight:600;letter-spacing:5px}
.brand span{display:block;font-size:8px;letter-spacing:4px;margin-top:4px}
.hero-title{left:150px;top:268px;font-size:56px;font-weight:700;color:transparent;-webkit-text-stroke:1.5px var(--gold);white-space:nowrap}
.hero-sub{left:154px;top:340px;font-size:27px;font-weight:600;color:var(--gold)}
.link-cta{font-size:10px;font-weight:600;letter-spacing:2.5px;padding-left:16px;border-left:2px solid var(--gold);line-height:14px}
.hero-watch{left:152px;top:480px;color:var(--ink)}
.slide-count{left:1056px;top:314px;color:var(--white);font-size:22px;font-weight:500}
.slide-count small{font-size:10px}

/* services */
.services{position:absolute;left:0;top:650px;width:1200px;height:962px;background:var(--mist)}
.sec-title{font-size:28px;font-weight:600;color:var(--ink)}
.card{position:absolute;background:var(--espresso);color:#e8e2dc;padding:0 36px}
.card h3{font-size:17px;font-weight:600;color:var(--gold);line-height:21px}
.card p{font-size:11.5px;line-height:20px;margin-top:10px;color:#d8d1ca}
.card .link-cta{margin-top:24px;display:block;color:var(--white)}

/* experience */
.experience{position:absolute;left:0;top:1612px;width:1200px;height:457px;
  background:
    radial-gradient(ellipse 35% 30% at 50% 100%,rgba(92,110,60,.75),rgba(92,110,60,0) 100%),
    radial-gradient(ellipse 25% 40% at 85% 60%,rgba(40,40,40,.7),rgba(40,40,40,0) 100%),
    linear-gradient(180deg,#4a4b4d 0%,#56575a 40%,#3f423c 80%,#33372e 100%)}
.big-num{left:96px;top:45px;font-size:380px;font-weight:700;line-height:300px;color:rgba(200,200,200,.55);letter-spacing:-10px}
.exp-title{left:268px;top:195px;font-size:28px;font-weight:600;color:var(--white);line-height:31px}
.exp-lead{left:601px;top:96px;width:447px;font-size:17px;line-height:26px;color:var(--white);text-align:justify}
.exp-lead em{font-style:normal;color:var(--gold);font-weight:600}
.exp-body{left:601px;top:197px;width:447px;font-size:11px;line-height:20px;color:#ddd;text-align:justify}
.exp-link{left:601px;top:336px;color:var(--white)}

/* projects */
.projects{position:absolute;left:0;top:2069px;width:1200px;height:711px}
.proj-photo{left:268px;top:174px;width:664px;height:434px;box-shadow:0 20px 40px rgba(0,0,0,.12);
  background:
    radial-gradient(ellipse 22% 30% at 32% 45%,rgba(235,228,220,.7),rgba(235,228,220,0) 100%),
    radial-gradient(ellipse 14% 18% at 24% 75%,rgba(170,40,40,.65),rgba(170,40,40,0) 100%),
    radial-gradient(ellipse 30% 40% at 50% 10%,rgba(110,140,80,.7),rgba(110,140,80,0) 100%),
    radial-gradient(ellipse 25% 45% at 62% 70%,rgba(20,20,20,.8),rgba(20,20,20,0) 100%),
    linear-gradient(140deg,#4d5640 0%,#2e2a25 50%,#3b3733 100%)}
.proj-label{left:200px;top:550px;transform:rotate(-90deg);transform-origin:left top;font-size:17px;font-weight:600;white-space:nowrap;color:var(--ink)}
.proj-label span{color:var(--gold)}
.ghost-num{font-size:48px;font-weight:700;color:transparent;-webkit-text-stroke:1.2px var(--gold)}

/* testimonial */
.testimonial{position:absolute;left:0;top:2780px;width:1200px;height:398px;background:var(--mist);text-align:center}
.testimonial p{position:absolute;left:200px;top:95px;width:800px;font-size:18px;line-height:31px;color:var(--muted)}
.quote-mark{color:var(--gold);font-size:16px;font-weight:700;vertical-align:top;line-height:20px}
.avatar{left:570px;top:233px;width:60px;height:60px;border-radius:50%;
  background:radial-gradient(circle at 40% 35%,#d9c8b2,#8a7564 55%,#4a3f38)}
.t-name{left:0;top:313px;width:1200px;font-size:13px;font-weight:600}

/* photography */
.photography{position:absolute;left:0;top:3178px;width:1200px;height:615px}
.gallery-img{top:150px;width:283px;height:283px}
.gallery-name{top:460px;font-size:17px;font-weight:600}
.gallery-text{top:490px;width:230px;font-size:11.5px;line-height:20px;color:var(--muted)}

/* cta */
.cta-band{position:absolute;left:0;top:3793px;width:1200px;height:153px;background:var(--gold-band)}
.cta-band h2{position:absolute;left:292px;top:58px;font-size:26px;font-weight:600;color:var(--espresso)}
.cta-btn{position:absolute;left:689px;top:52px;width:191px;height:49px;background:var(--espresso);color:var(--gold);font-size:12px;font-weight:500;display:flex;align-items:center;justify-content:center;letter-spacing:.5px}

/* footer */
.footer{position:absolute;left:0;top:3946px;width:1200px;height:255px;background:var(--espresso);color:var(--white)}
.foot-brand{left:153px;top:100px;font-size:34px;font-weight:700;color:var(--gold);letter-spacing:3px}
.foot-label{font-size:11px;font-weight:600;letter-spacing:2.5px}
.foot-big{font-size:18px}
.foot-small{font-size:11.5px;color:#ddd}
.foot-rule{left:78px;top:193px;width:1044px;height:1px;background:rgba(255,255,255,.15)}
.copyright{left:153px;top:226px;font-size:10px;color:#ccc}
.social{top:215px;width:28px;height:28px;border-radius:50%;background:#5d544f;display:flex;align-items:center;justify-content:center}
</style>
</head>
<body>

<header class="hero">
  <div class="photo hero-photo" role="img" aria-label="Bride and groom embracing beside a waterfall at sunset"></div>
  <nav class="nav left"><a class="active">Films</a><i class="dot"></i><a>Prices</a><i class="dot"></i><a>Reviews</a></nav>
  <div class="brand"><b>BMRT</b><span>WEDDING FILMS</span></div>
  <nav class="nav right"><a>Options</a><i class="dot"></i><a>About</a><i class="dot"></i><a>Contact</a></nav>
  <h1 class="abs hero-title">Unique Wedding</h1>
  <div class="abs hero-sub">Video and Photography</div>
  <div class="abs link-cta hero-watch">WATCH VIDEO</div>
  <svg class="abs" style="left:1080px;top:270px" width="16" height="10" viewBox="0 0 16 10"><path d="M1 9l7-7 7 7" fill="none" stroke="#fff" stroke-width="1.5"/></svg>
  <div class="abs slide-count">01 <small>/ 06</small></div>
  <svg class="abs" style="left:1080px;top:365px" width="16" height="10" viewBox="0 0 16 10"><path d="M1 1l7 7 7-7" fill="none" stroke="#fff" stroke-width="1.5"/></svg>
</header>

<section class="services">
  <h2 class="abs sec-title" style="left:153px;top:138px">What Can We Do</h2>
  <div class="photo" style="left:600px;top:122px;width:332px;height:359px;background:radial-gradient(ellipse 30% 25% at 70% 70%,rgba(200,200,210,.7),rgba(200,200,210,0)),radial-gradient(ellipse 40% 30% at 85% 15%,rgba(220,200,200,.6),rgba(220,200,200,0)),linear-gradient(160deg,#6e6450 0%,#9a8a62 50%,#5e5a40 100%)" role="img" aria-label="Engagement ring close-up with flowers"></div>
  <div class="photo" style="left:268px;top:250px;width:332px;height:360px;background:radial-gradient(ellipse 30% 45% at 70% 60%,rgba(238,230,215,.85),rgba(238,230,215,0)),radial-gradient(ellipse 25% 30% at 35% 35%,rgba(120,80,50,.8),rgba(120,80,50,0)),linear-gradient(160deg,#5d6a48 0%,#9a7f62 45%,#b49a7a 100%)" role="img" aria-label="Couple laughing under falling confetti"></div>
  <div class="photo" style="left:600px;top:481px;width:332px;height:357px;background:radial-gradient(ellipse 30% 50% at 65% 65%,rgba(235,232,228,.85),rgba(235,232,228,0)),radial-gradient(ellipse 25% 25% at 40% 35%,rgba(90,70,60,.7),rgba(90,70,60,0)),linear-gradient(180deg,#7d858a 0%,#4d5558 45%,#6a6a62 100%)" role="img" aria-label="Groom kissing bride by the sea"></div>
  <div class="card" style="left:535px;top:57px;width:283px;height:282px;padding-top:67px">
    <h3>Creative<br>Conceptions</h3>
    <p>Sed do eiusmod tempor<br>incididunt ut labore<br>dolore magna ...</p>
    <span class="link-cta">MORE</span>
  </div>
  <div class="card" style="left:230px;top:418px;width:230px;height:230px;padding-top:47px">
    <h3>Shooting &amp;<br>Editing</h3>
    <p>Sed do eiusmod tempor<br>incididunt ut labore<br>dolore magna ...</p>
    <span class="link-cta">MORE</span>
  </div>
  <div class="card" style="left:562px;top:648px;width:229px;height:229px;padding-top:47px">
    <h3>Unique<br>Photography</h3>
    <p>Sed do eiusmod tempor<br>incididunt ut labore<br>dolore magna ...</p>
    <span class="link-cta">MORE</span>
  </div>
</section>

<section class="experience" role="img" aria-label="Videographer filming a couple walking through a field under stormy sky">
  <div class="abs big-num">13</div>
  <h2 class="abs exp-title">Years of Successful<br>experience</h2>
  <p class="abs exp-lead">Sed ut perspiciatis <em>unde omnis iste natus</em> error sit voluptatem doloremque laudantium, <em>ipsa quae ab illo inventore</em> veritatis et quasi</p>
  <p class="abs exp-body">Nemo enim ipsam voluptatem quia voluptas sit aspernatur aut odit aut fugit, sed quia consequuntur magni dolores eos qui ratione voluptatem sequi nesciunt. Neque porro quisquam est, qui dolorem ipsum quia dolor sit amet, consectetur, adipisci velit, sed quia non numquam eius modi tempora incidunt ut labore et dolore magnam</p>
  <div class="abs link-cta exp-link">ABOUT US</div>
</section>

<section class="projects">
  <h2 class="abs sec-title" style="left:150px;top:84px">Latest Projects</h2>
  <div class="abs ghost-num" style="left:258px;top:148px">2</div>
  <div class="photo proj-photo" role="img" aria-label="Bride and groom walking through a shower of petals with guests"></div>
  <svg class="abs" style="left:560px;top:370px" width="80" height="80" viewBox="0 0 80 80"><circle cx="40" cy="40" r="40" fill="rgba(255,255,255,.18)"/><path d="M32 26l20 14-20 14z" fill="none" stroke="#fff" stroke-width="2"/></svg>
  <div class="abs ghost-num" style="left:908px;top:570px;color:var(--gold);-webkit-text-stroke:0">4</div>
  <div class="abs proj-label"><span>03.</span> Rosa &amp; Liam Harte</div>
  <svg class="abs" style="left:203px;top:175px" width="10" height="18" viewBox="0 0 10 18"><path d="M9 1L1 9l8 8" fill="none" stroke="#ccc" stroke-width="1.5"/></svg>
  <svg class="abs" style="left:985px;top:590px" width="10" height="18" viewBox="0 0 10 18"><path d="M1 1l8 8-8 8" fill="none" stroke="#333" stroke-width="1.5"/></svg>
</section>

<section class="testimonial">
  <p><span class="quote-mark">&ldquo;</span> Sed ut perspiciatis unde omnis iste natus error sit voluptatem<br>accusantium doloremque laudantium, totam rem aperiam, eaque ipsa<br>quae ab illo inventore veritatis et quasi architecto<br>beatae vitae dicta sunt explicabo <span class="quote-mark">&rdquo;</span></p>
  <div class="abs avatar" role="img" aria-label="Portrait of the reviewer"></div>
  <div class="abs t-name">Elena Marwick</div>
</section>

<section class="photography">
  <h2 class="abs sec-title" style="left:150px;top:99px">Photography</h2>
  <svg class="abs" style="left:108px;top:286px" width="10" height="18" viewBox="0 0 10 18"><path d="M9 1L1 9l8 8" fill="none" stroke="#ccc" stroke-width="1.5"/></svg>
  <div class="photo gallery-img" style="left:153px;background:radial-gradient(ellipse 35% 40% at 45% 75%,rgba(240,238,232,.95),rgba(240,238,232,0)),radial-gradient(ellipse 25% 45% at 80% 75%,rgba(40,45,70,.85),rgba(40,45,70,0)),linear-gradient(180deg,#6f7a4e 0%,#a4a07c 45%,#8a8466 100%)" role="img" aria-label="Smiling bride held by groom in a garden"></div>
  <div class="photo gallery-img" style="left:459px;background:radial-gradient(ellipse 30% 45% at 40% 55%,rgba(245,245,245,.9),rgba(245,245,245,0)),radial-gradient(ellipse 20% 50% at 85% 50%,rgba(30,30,30,.85),rgba(30,30,30,0)),linear-gradient(180deg,#c4c4c4 0%,#9a9a9a 60%,#6a6a6a 100%)" role="img" aria-label="Black and white photo of a couple walking through smoke"></div>
  <div class="photo gallery-img" style="left:764px;background:radial-gradient(ellipse 25% 40% at 40% 70%,rgba(170,190,200,.9),rgba(170,190,200,0)),radial-gradient(ellipse 25% 50% at 70% 60%,rgba(180,170,150,.8),rgba(180,170,150,0)),linear-gradient(180deg,#8fa08a 0%,#6f8060 50%,#4e5c3e 100%)" role="img" aria-label="Couple holding a bouquet on a hillside"></div>
  <svg class="abs" style="left:1080px;top:286px" width="10" height="18" viewBox="0 0 10 18"><path d="M1 1l8 8-8 8" fill="none" stroke="#333" stroke-width="1.5"/></svg>
  <div class="abs gallery-name" style="left:153px;color:var(--gold)">Nora &amp; Theo</div>
  <div class="abs gallery-name" style="left:459px">Rosa &amp; Liam</div>
  <div class="abs gallery-name" style="left:764px">Nora &amp; Theo</div>
  <p class="abs gallery-text" style="left:153px">Lorem Ipsum is simply dummy text printing and typesettin</p>
  <p class="abs gallery-text" style="left:459px">Lorem Ipsum is simply dummy text printing and typesettin</p>
  <p class="abs gallery-text" style="left:764px">Lorem Ipsum is simply dummy text printing and typesettin</p>
</section>

<section class="cta-band">
  <h2>Start your project with us</h2>
  <div class="cta-btn">Get Started Now!</div>
</section>

<footer class="footer">
  <div class="abs foot-brand">BMRT</div>
  <div class="abs foot-label" style="left:352px;top:64px">CONTACT US</div>
  <div class="abs foot-big" style="left:352px;top:97px">Call. <span style="color:var(--gold)">+1 800 555 0142</span></div>
  <div class="abs foot-small" style="left:352px;top:128px">e. hello@bmrtfilms.example</div>
  <div class="abs foot-label" style="left:646px;top:64px">GET IN TOUCH</div>
  <div class="abs foot-big" style="left:646px;top:97px">Studio 14 Larch Yard,</div>
  <div class="abs foot-small" style="left:646px;top:128px">Mill Lane, London 20417</div>
  <svg class="abs" style="left:1028px;top:68px" width="14" height="20" viewBox="0 0 14 20"><path d="M7 19V2M1 8l6-6 6 6" fill="none" stroke="var(--gold)" stroke-width="1.5"/></svg>
  <div class="abs foot-rule"></div>
  <div class="abs copyright">2020 &copy; BMRT Wedding Films. All Rights Reserved.</div>
  <div class="abs social" style="left:903px" aria-label="Email"><svg width="12" height="9" viewBox="0 0 12 9"><rect x=".5" y=".5" width="11" height="8" fill="none" stroke="#fff"/><path d="M.5 .5l5.5 4.5 5.5-4.5" fill="none" stroke="#fff"/></svg></div>
  <div class="abs social" style="left:941px" aria-label="Share"><svg width="12" height="12" viewBox="0 0 12 12"><circle cx="2.5" cy="6" r="1.6" fill="#fff"/><circle cx="9.5" cy="2.5" r="1.6" fill="#fff"/><circle cx="9.5" cy="9.5" r="1.6" fill="#fff"/><path d="M2.5 6l7-3.5M2.5 6l7 3.5" stroke="#fff"/></svg></div>
  <div class="abs social" style="left:979px" aria-label="Website"><svg width="12" height="12" viewBox="0 0 12 12"><circle cx="6" cy="6" r="5" fill="none" stroke="#fff"/><path d="M1 6h10M6 1c-2.5 3-2.5 7 0 10M6 1c2.5 3 2.5 7 0 10" fill="none" stroke="#fff" stroke-width=".8"/></svg></div>
  <div class="abs social" style="left:1017px" aria-label="Phone"><svg width="12" height="12" viewBox="0 0 12 12"><path d="M2 1h2.5l1 3-1.5 1c.7 1.4 1.6 2.3 3 3l1-1.5 3 1V11c-5 0-10-5-10-10z" fill="#fff"/></svg></div>
</footer>

</body>
</html>
```